Commercial Swimming Pool - Design-Build Contractor Website Design

I need a new website that will feature our newly developed logo and trade name as well as provide a fully updated site experience. We are not a residential builder - we strictly design and install high-end commercial pools. I need the website to highlight our portfolio and communicate the various types of projects in which we specialize. I want the effect of the site to reflect the high-end nature of our services - projects like the 57th floor spa at the Phila Silver Willow, the aquatic therapy portion of the Phila Ravenhawks training facility, a 5om indoor competition pool for the prestigious Dallowmere Academy, the indoor water park at The Quenwick Lodge or the recent country club renovation projects we've completed in our region (to name a few examples).
Need extra days to review

```html
<!DOCTYPE html>
<html lang="en">
<head>
<meta charset="utf-8">
<title>Corvane Aquatics — Commercial Pool Design &amp; Construction</title>
<link href="https://fonts.googleapis.com/css2?family=Kanit:wght@600;700&family=Lato:wght@400;700&display=swap" rel="stylesheet">
<style>
:root{
  --navy:#0c2a6e;
  --navy-deep:#071a47;
  --night:#061335;
  --sky:#4bb5e8;
  --sky-light:#7fd0f5;
  --pool:#1f8fd6;
  --white:#ffffff;
  --ink:#1b2433;
  --cta:#53bde9;
}
*{margin:0;padding:0;box-sizing:border-box}
html,body{width:1200px;height:3934px;overflow:hidden}
body{position:relative;background:var(--navy);font-family:"Lato",sans-serif;color:var(--white)}
.abs{position:absolute}
.btn{position:absolute;display:flex;align-items:center;justify-content:center;border-radius:24px;background:var(--cta);color:var(--white);font-family:"Lato",sans-serif;font-weight:700;font-size:15px}
.display{font-family:"Kanit",sans-serif;font-weight:700;text-transform:uppercase;letter-spacing:1px;line-height:1}

/* hero */
.hero{left:0;top:0;width:1200px;height:710px;background:linear-gradient(160deg,#3d6fc4 0%,#2853a8 40%,#1d439a 70%,#163a8c 100%)}
.brand{font-family:"Lato",sans-serif;font-weight:700;color:var(--white);text-transform:uppercase;letter-spacing:2px;white-space:nowrap}
.brand-head{left:110px;top:55px;font-size:26px;display:flex;align-items:center;gap:12px}
.brand-mark{width:14px;height:14px;background:var(--white)}
.quote-btn{left:953px;top:34px;width:137px;height:44px;background:var(--white);color:var(--ink);font-weight:400;font-size:15px}
.nav{top:96px;font-size:17px;font-weight:700}
.hero-title{right:110px;top:218px;font-size:68px;text-align:right;line-height:1.32}
.hero-text{right:110px;top:403px;width:460px;text-align:right;font-size:15px;line-height:26px}
.hero-btn{left:921px;top:510px;width:169px;height:46px}

/* about */
.about{left:0;top:690px;width:1200px;height:730px;background:linear-gradient(180deg,#0b2a6d 0%,#0d2d74 60%,#0b286a 100%)}
.about-title{left:110px;top:840px;font-size:46px}
.about-text{left:110px;top:920px;width:475px;font-size:16px;line-height:31px}
.read-btn{left:111px;top:1201px;width:118px;height:47px}
.about-ring{left:645px;top:829px;width:436px;height:436px;border-radius:50%;background:var(--sky)}
.about-photo{left:667px;top:851px;width:392px;height:392px;border-radius:50%;background:radial-gradient(circle at 50% 35%,#d8cfc3 0%,#b9aa98 45%,#5cb8d6 75%,#2d97c6 100%)}

/* projects */
.projects{left:0;top:1412px;width:1200px;height:780px;background:linear-gradient(180deg,#3fa5e0 0%,#4bb0e6 50%,#3aa0dc 100%)}
.section-title{left:0;width:1200px;text-align:center;font-size:48px}
.section-sub{left:160px;width:880px;text-align:center;font-size:16px;line-height:30px}
.proj-card{top:1684px;width:305px;height:331px;background:var(--white);border-radius:6px}
.proj-photo{position:absolute;left:8px;top:9px;width:289px;height:231px;border-radius:6px}
.proj-cap{position:absolute;left:10px;right:10px;top:253px;text-align:center;color:var(--ink);font-size:17px;line-height:29px}
.arrow{top:2056px;width:28px;height:28px}

/* portfolio */
.portfolio{left:0;top:2192px;width:1200px;height:1240px;background:linear-gradient(180deg,#0a2565 0%,#0c2a6e 50%,#0a2262 100%)}
.port-card{width:268px;height:336px;background:var(--white);padding:7px}
.port-photo{width:100%;height:100%;position:relative}
.port-cap{position:absolute;left:11px;right:11px;bottom:22px;height:64px;background:var(--white);display:flex;align-items:center;justify-content:center;text-align:center;color:var(--ink);font-size:13px;line-height:20px;padding:0 14px}
.start-btn{left:541px;top:3259px;width:118px;height:44px}

/* footer */
.footer{left:0;top:3432px;width:1200px;height:502px;background:linear-gradient(180deg,#081b48 0%,#061335 40%,#050f2b 100%)}
.brand-foot{left:0;width:1200px;top:3560px;font-size:40px;display:flex;justify-content:center;align-items:center;gap:16px}
.brand-foot .brand-mark{width:20px;height:20px}
.contact-bar{left:110px;top:3695px;width:978px;height:107px;border:1px solid rgba(255,255,255,.18);display:flex}
.contact-cell{position:relative;height:100%;display:flex;align-items:center;gap:26px;padding-left:24px}
.contact-cell + .contact-cell{border-left:1px solid rgba(255,255,255,.18)}
.contact-label{font-size:17px;font-weight:700;margin-bottom:6px}
.contact-val{font-size:13px}
.social{left:570px;top:3839px;width:30px;height:30px;border-radius:50%;background:var(--sky)}
.copyright{left:0;width:1200px;top:3883px;text-align:center;font-size:15px}
</style>
</head>
<body>

<!-- hero -->
<div class="abs hero" role="img" aria-label="Sunlit blue mosaic pool tiles with sunglasses, a straw hat and a summer drink at the pool edge"></div>
<div class="abs brand brand-head"><span class="brand-mark"></span>Corvane Aquatics</div>
<div class="btn quote-btn">Get A Quote</div>
<div class="abs nav" style="left:478px">Home</div>
<div class="abs nav" style="left:594px">About Us</div>
<div class="abs nav" style="left:735px">Projects</div>
<div class="abs nav" style="left:868px">Portfolio</div>
<div class="abs nav" style="left:1006px">Contact Us</div>
<h1 class="abs display hero-title">Welcome to<br>Corvane Aquatics</h1>
<p class="abs hero-text">But I must explain to you how all this mistaken idea of denouncing pleasure and praising pain was born and I will give you a complete account of the system, and expound th</p>
<div class="btn hero-btn">Get Started Now</div>

<!-- about -->
<section class="abs about"></section>
<svg class="abs" style="left:0;top:660px" width="1200" height="60" viewBox="0 0 1200 60" aria-hidden="true"><path d="M0 40 L150 30 L320 42 L520 28 L760 40 L980 30 L1200 38 L1200 60 L0 60Z" fill="#0b2a6d"/></svg>
<h2 class="abs display about-title">About Us</h2>
<p class="abs about-text">"But I must explain to you how all this mistaken idea of denouncing pleasure and praising pain was born and I will give you a complete account of the system, and expound the actual teachings of the great explorer of the truth, the master-builder of human happiness. No one rejects, dislikes, or avoids pleasure itself, because it is pleasure, but because those who do not know how to pursue pleasure rationally encounter consequences that are extremely painful.</p>
<div class="btn read-btn">Read More</div>
<div class="abs about-ring"></div>
<div class="abs about-photo" role="img" aria-label="Technician installing a stainless steel handrail beside a small spa pool"></div>

<!-- projects -->
<section class="abs projects" role="img" aria-label="Bright blue resort pool scene with palm trees behind the section"></section>
<svg class="abs" style="left:0;top:1395px" width="1200" height="40" viewBox="0 0 1200 40" aria-hidden="true"><path d="M0 20 L200 12 L420 24 L640 14 L880 22 L1080 12 L1200 18 L1200 40 L0 40Z" fill="#3fa5e0"/></svg>
<h2 class="abs display section-title" style="top:1512px">Our Projects</h2>
<p class="abs section-sub" style="top:1580px">"But I must explain to you how all this mistaken idea of denouncing pleasure and praising pain was born and I will give you a complete account of the system, and expound the actual teachings</p>

<div class="abs proj-card" style="left:107px">
  <div class="proj-photo" role="img" aria-label="Rooftop spa pool with lounge chairs and umbrellas" style="background:linear-gradient(180deg,#8aa872 0%,#6f8f5d 35%,#45c9ef 60%,#2fb8ea 100%)"></div>
  <p class="proj-cap">57th floor spa at the Phila Silver Willow</p>
</div>
<div class="abs proj-card" style="left:447px">
  <div class="proj-photo" role="img" aria-label="Group of swimmers in an outdoor therapy pool" style="background:linear-gradient(180deg,#c9d6df 0%,#9fb8c4 30%,#5cc3e6 60%,#3fb0e0 100%)"></div>
  <p class="proj-cap">Aquatic therapy portion of the Phila Ravenhawks training facility</p>
</div>
<div class="abs proj-card" style="left:788px">
  <div class="proj-photo" role="img" aria-label="Swimmers gliding underwater in a deep blue pool" style="background:linear-gradient(180deg,#2a66c9 0%,#1c53b8 50%,#0f3c9a 100%)"></div>
  <p class="proj-cap">Indoor water park at The Quenwick Lodge</p>
</div>
<svg class="abs arrow" style="left:566px" viewBox="0 0 28 28" aria-label="Previous"><circle cx="14" cy="14" r="14" fill="#ffffff"/><path d="M16 8 L10 14 L16 20" stroke="#0c2a6e" stroke-width="3" fill="none" stroke-linecap="round" stroke-linejoin="round"/></svg>
<svg class="abs arrow" style="left:605px" viewBox="0 0 28 28" aria-label="Next"><circle cx="14" cy="14" r="14" fill="#ffffff"/><path d="M12 8 L18 14 L12 20" stroke="#0c2a6e" stroke-width="3" fill="none" stroke-linecap="round" stroke-linejoin="round"/></svg>

<!-- portfolio -->
<section class="abs portfolio"></section>
<svg class="abs" style="left:0;top:2172px" width="1200" height="40" viewBox="0 0 1200 40" aria-hidden="true"><path d="M0 20 L220 28 L460 16 L700 26 L940 16 L1200 24 L1200 40 L0 40Z" fill="#0a2565"/></svg>
<h2 class="abs display section-title" style="top:2316px">Portfolio</h2>
<p class="abs section-sub" style="top:2384px">"But I must explain to you how all this mistaken idea of denouncing pleasure and praising pain was born and I will give you a complete account of the system, and expound the actual teachings</p>

<div class="abs port-card" style="left:5px;top:2500px"><div class="port-photo" role="img" aria-label="Child splashing in a pool fountain" style="background:linear-gradient(160deg,#d9e4ea 0%,#8fc9e2 50%,#2b9fd4 100%)"><div class="port-cap">At vero eos et accusamus et lusto</div></div></div>
<div class="abs port-card" style="left:302px;top:2500px"><div class="port-photo" role="img" aria-label="Children with pool floats beside a swimming pool under blue sky" style="background:linear-gradient(180deg,#3e8fe0 0%,#7cc0ee 45%,#4f9a3c 70%,#35c2c9 100%)"><div class="port-cap">At vero eos et accusamus et lusto</div></div></div>
<div class="abs port-card" style="left:600px;top:2500px"><div class="port-photo" role="img" aria-label="Two children in goggles swimming in clear water" style="background:linear-gradient(180deg,#8fd3ef 0%,#4cb8e6 50%,#2b9fd8 100%)"><div class="port-cap">At vero eos et accusamus et lusto</div></div></div>
<div class="abs port-card" style="left:302px;top:2868px"><div class="port-photo" role="img" aria-label="Infinity pool with palm trees at dusk" style="background:linear-gradient(180deg,#8f9fd2 0%,#b09ac4 30%,#3b8fd0 55%,#9a8f86 80%,#7b6f66 100%)"><div class="port-cap">At vero eos et accusamus et lusto</div></div></div>
<div class="abs port-card" style="left:600px;top:2868px"><div class="port-photo" role="img" aria-label="Indoor lap pool with lit ceiling and stone walls" style="background:linear-gradient(180deg,#3a3f9a 0%,#5f6fc6 30%,#2060c6 60%,#0f4ab0 100%)"><div class="port-cap">At vero eos et accusamus et lusto</div></div></div>
<div class="abs port-card" style="left:898px;top:2868px"><div class="port-photo" role="img" aria-label="Workers inspecting a pool wall during construction" style="background:linear-gradient(180deg,#6f8f7e 0%,#4fb5c9 40%,#6fd0e8 70%,#8edcf0 100%)"><div class="port-cap">At vero eos et accusamus et lusto</div></div></div>

<div class="btn start-btn">Get Started</div>

<!-- footer -->
<footer class="abs footer"></footer>
<div class="abs brand brand-foot"><span class="brand-mark"></span>Corvane Aquatics</div>
<div class="abs contact-bar">
  <div class="contact-cell" style="width:327px">
    <svg width="60" height="60" viewBox="0 0 60 60" fill="none" stroke="#ffffff" stroke-width="2" aria-hidden="true"><rect x="8" y="22" width="20" height="34"/><rect x="28" y="8" width="24" height="48"/><path d="M2 56 H58"/><path d="M13 30h4M20 30h4M13 38h4M20 38h4M13 46h4M20 46h4M33 16h4M42 16h4M33 25h4M42 25h4M33 34h4M42 34h4M33 43h4M42 43h4"/></svg>
    <div class="contact-val" style="line-height:24px">14Y, Corvane Aquatics, At vero<br>eos et accusamus</div>
  </div>
  <div class="contact-cell" style="width:369px;padding-left:40px">
    <svg width="58" height="40" viewBox="0 0 58 40" fill="none" stroke="#ffffff" stroke-width="2" aria-hidden="true"><rect x="1" y="1" width="56" height="38"/><path d="M1 1 L29 24 L57 1M1 39 L22 18M57 39 L36 18"/></svg>
    <div><div class="contact-label">Email Us :</div><div class="contact-val">support@corvaneaquatics.com</div></div>
  </div>
  <div class="contact-cell" style="flex:1;padding-left:50px">
    <svg width="58" height="58" viewBox="0 0 58 58" fill="none" stroke="#ffffff" stroke-width="2" aria-hidden="true"><path d="M12 6 L20 16 L15 22 C18 30 26 38 34 42 L40 36 L50 44 L44 52 C26 50 8 32 6 14Z"/><rect x="30" y="4" width="24" height="16" rx="3"/><path d="M34 20 L32 26 L40 20"/><circle cx="37" cy="12" r="1"/><circle cx="42" cy="12" r="1"/><circle cx="47" cy="12" r="1"/></svg>
    <div><div class="contact-label">Call Us :</div><div class="contact-val">+1 555 0142-300</div></div>
  </div>
</div>
<div class="abs social" aria-label="Social profile"></div>
<p class="abs copyright">© 2023 Corvane Aquatics | All Rights Reserved.</p>

</body>
</html>
```